Polystyrene Environmental Synopsis

We need a fact sheet for quick reference that groups information units and has a simple but engaging visual presentation of the text and various infographics. We are a trade association representing polystyrene foam manufacturers and this piece is intended to help our members provide effective messaging to their sales personnel.

To view our typical company design/style please see our website at www.flarenticouncil.org. Our primary RGB colors are: (187,140,9); (94,47,29); (94,138,164); and (164,167,15). Secondary RGB colors are (249,162,28) and (218,210,208). Our title/header font is DIN Next LT Pro and our copy font is Calibri 10.5 pt. We can deviate from the font specification if beneficial.

Target Market(s)

Polystyrene manufacturer plant workers and other employees.

Font styles to use
Sans Serif

Requirements
Must have
• Information presentation must be clean and easy to reference.

```html
<!DOCTYPE html>
<html lang="en">
<head>
<meta charset="utf-8">
<title>Recycling – Polystyrene Environmental Synopsis</title>
<link href="https://fonts.googleapis.com/css2?family=Barlow+Semi+Condensed:wght@500;600;700&family=Open+Sans:wght@400;700&display=swap" rel="stylesheet">
<style>
  :root{
    --olive:#a4a70f;
    --olive-light:#c3c25a;
    --brown:#5e2f1d;
    --gold:#bb8c09;
    --ink:#1c1c1c;
    --paper:#ffffff;
  }
  *{margin:0;padding:0;box-sizing:border-box}
  html,body{width:848px;height:1200px;overflow:hidden;background:var(--paper)}
  .sheet{position:relative;width:848px;height:1200px;overflow:hidden;font-family:"Open Sans",sans-serif;color:var(--ink)}
  .top-band{position:absolute;left:0;top:0;width:848px;height:26px;background:var(--olive)}
  .section-tab{position:absolute;right:0;top:0;width:200px;height:50px;background:var(--olive-light);
    font-family:"Barlow Semi Condensed",sans-serif;font-weight:700;font-size:21px;color:var(--brown);
    display:flex;align-items:center;justify-content:flex-end;padding-right:22px;letter-spacing:.5px}
  .spine{position:absolute;left:28px;top:26px;width:6px;height:1160px;background:var(--gold)}
  .panel{position:absolute;left:31px;width:222px;background:var(--brown);border-radius:0 30px 0 0;
    box-shadow:4px 0 0 #4a2415;display:flex;align-items:center;justify-content:flex-end;padding-right:14px}
  .panel h2{font-family:"Barlow Semi Condensed",sans-serif;font-weight:500;color:#fff;font-size:25px;line-height:1.25;text-align:right;letter-spacing:.5px}
  .p1{top:64px;height:502px}
  .p2{top:583px;height:271px}
  .p3{top:889px;height:299px}
  .fact{position:absolute;width:210px;text-align:center;font-size:11.5px;line-height:1.4;text-transform:uppercase;font-weight:700}
  .fact svg{display:block;margin:0 auto 8px}
  .hl{color:var(--brown)}
  .icon{fill:none;stroke:var(--olive);stroke-width:3;stroke-linecap:round;stroke-linejoin:round}
  .f1{left:312px;top:76px}
  .f2{left:578px;top:60px}
  .f3{left:312px;top:300px}
  .f4{left:578px;top:292px}
  .f5{left:312px;top:612px}
  .f6{left:578px;top:626px}
  .box-icon{position:absolute;left:405px;top:914px}
  .box-text{position:absolute;left:512px;top:938px;width:150px;font-size:11.5px;line-height:1.4;font-weight:700;text-transform:uppercase}
  .markets-title{position:absolute;left:320px;top:1050px;font-size:11.5px;font-weight:700;color:var(--brown);text-transform:uppercase}
  .market-list{position:absolute;list-style:none;font-size:11.5px;font-weight:700;text-transform:uppercase;line-height:1.55}
  .market-list li{position:relative;padding-left:14px}
  .market-list li::before{content:"";position:absolute;left:0;top:1px;width:5px;height:5px;border-radius:50%;background:var(--olive)}
  .ml1{left:324px;top:1090px}
  .ml2{left:493px;top:1092px}
</style>
</head>
<body>
<div class="sheet">
  <div class="top-band"></div>
  <div class="section-tab">RECYCLING</div>
  <div class="spine"></div>

  <div class="panel p1"><h2>EPS IS<br>RECYCLABLE</h2></div>
  <div class="panel p2"><h2>NEW EPS<br>RECYCLING<br>TECHNOLOGIES<br>ARE EMERGING</h2></div>
  <div class="panel p3"><h2>EPS<br>END-MARKETS<br>SHOW<br>CONSISTENT<br>GROWTH</h2></div>

  <div class="fact f1">
    <svg width="90" height="86" viewBox="0 0 90 86" class="icon">
      <path d="M34 12 L45 4 L56 12 L48 12 L60 34"/><path d="M30 36 L40 18"/>
      <path d="M70 44 L80 62 L70 76 L56 76"/><path d="M62 70 L56 76 L62 82"/>
      <path d="M36 76 L14 76 L6 62 L18 42"/><path d="M10 44 L18 42 L22 50"/>
    </svg>
    Historically, EPS recycling averages<br><span class="hl">~18%</span> over a<br><span class="hl">25-year trendline.</span>
  </div>

  <div class="fact f2">
    <svg width="70" height="96" viewBox="0 0 70 96" class="icon">
      <circle cx="35" cy="32" r="26"/><circle cx="35" cy="32" r="17"/>
      <path d="M35 22 L38 29 L45 29 L39 34 L41 41 L35 37 L29 41 L31 34 L25 29 L32 29 Z"/>
      <path d="M20 54 L14 90 L24 82 L32 92 L34 60"/><path d="M50 54 L56 90 L46 82 L38 92 L36 60"/>
    </svg>
    <span class="hl">EPS recycling is<br>most successful</span><br>in commercial waste streams with large volume sources of EPS waste.
  </div>

  <div class="fact f3">
    <svg width="110" height="90" viewBox="0 0 110 90" class="icon">
      <circle cx="28" cy="20" r="12"/><circle cx="82" cy="20" r="12"/><circle cx="55" cy="30" r="14"/>
      <path d="M6 70 V48 Q6 36 20 36 H36"/><path d="M104 70 V48 Q104 36 90 36 H74"/>
      <path d="M30 86 V62 Q30 48 44 48 H66 Q80 48 80 62 V86 Z"/>
    </svg>
    Consumer <span class="hl">access to EPS recycling</span> sometimes requires extra effort, but with proper equipment &amp; handling, <span class="hl">it is successful in many communities.</span>
  </div>

  <div class="fact f4">
    <svg width="80" height="96" viewBox="0 0 80 96" class="icon">
      <path d="M40 8 A28 28 0 0 0 22 58 V70 H58 V58 A28 28 0 0 0 40 8"/>
      <path d="M26 78 H54"/><path d="M30 86 H50"/>
      <path d="M44 8 V22 H58 Q62 16 66 20 Q68 26 62 28 V36 H74"/>
    </svg>
    Creative <span class="hl">problem solving</span> for challenging recycling scenarios means Brightmart, Nutrivale, Harlow Kitchen, Coldstream, Voltline, Prairie Cuts are <span class="hl">committed to long term EPS recycling.</span>
  </div>

  <div class="fact f5">
    <svg width="40" height="100" viewBox="0 0 40 100" class="icon">
      <path d="M14 66 V12 A6 6 0 0 1 26 12 V66 A14 14 0 1 1 14 66 Z"/>
      <circle cx="20" cy="78" r="6"/><path d="M20 72 V30"/>
      <path d="M26 24 H32"/><path d="M26 36 H32"/><path d="M26 48 H32"/>
    </svg>
    <span class="hl">Pyrolysis—a chemical reprocessing method—</span><br>increases the ability to recycle contaminated EPS waste.
  </div>

  <div class="fact f6">
    <svg width="100" height="84" viewBox="0 0 100 84" class="icon">
      <path d="M6 80 V40 L30 52 V40 L54 52 V40 L78 52 V10 H92 V80 Z"/>
      <rect x="18" y="62" width="12" height="12"/><rect x="42" y="62" width="12" height="12"/><rect x="66" y="62" width="12" height="12"/>
    </svg>
    <span class="hl">Two new facilities</span><br>opened in 2018.
  </div>

  <svg class="box-icon icon" width="100" height="86" viewBox="0 0 100 86">
    <path d="M10 26 L50 10 L90 26 L90 66 L50 82 L10 66 Z"/>
    <path d="M10 26 L50 42 L90 26"/><path d="M50 42 V82"/>
    <path d="M28 18 L68 34 V50"/><path d="M36 15 L76 31"/>
  </svg>
  <div class="box-text">It is used as <span class="hl">recycled content in new EPS packaging</span> and other EPS products.</div>

  <div class="markets-title">Markets for recycled content EPS include:</div>
  <ul class="market-list ml1"><li>Crown molding</li><li>Picture frames</li></ul>
  <ul class="market-list ml2"><li>Surfboards</li><li>Other rigid polystyrene applications</li></ul>
</div>
</body>
</html>
```